Structural Engineering Business Card

Brookvane Drafting does residential house plans for clients in Central Florida. Would like simple but elegant business card that is appropriate for a house plan engineering company. Prefer black business card with black/white them but open to other shades of blue. I uploaded a sample card that I came across that looked good but please come up with your own creative designs.

Contact Information for Business Card

Name, Title, Phone, Email, Address, website

```html
<!DOCTYPE html>
<html lang="en">
<head>
<meta charset="utf-8">
<title>Brookvane Drafting – Business Card</title>
<link rel="stylesheet" href="https://fonts.googleapis.com/css2?family=Poppins:wght@400;700&display=swap">
<style>
  :root {
    --backdrop: #2b2b2b;
    --card-light: #f4f4f4;
    --card-dark: #0b0b0b;
    --ink: #111111;
    --paper: #ffffff;
    --rule: #1a1a1a;
  }
  * { margin: 0; padding: 0; box-sizing: border-box; }
  html, body {
    width: 1200px;
    height: 900px;
    overflow: hidden;
    background: var(--backdrop);
    font-family: "Poppins", sans-serif;
  }
  .canvas {
    width: 1200px;
    height: 900px;
    display: flex;
    align-items: center;
    justify-content: center;
    gap: 40px;
  }
  .card {
    width: 540px;
    height: 309px;
    position: relative;
    box-shadow: 0 14px 30px rgba(0, 0, 0, 0.45);
  }

  /* Front: contact side */
  .card--front {
    background: var(--card-light);
    color: var(--ink);
    display: flex;
    align-items: center;
  }
  .card__brand {
    width: 250px;
    display: flex;
    align-items: center;
    justify-content: center;
    gap: 8px;
  }
  .brand-mark {
    width: 12px;
    height: 12px;
    background: currentColor;
    flex: none;
  }
  .brand-name {
    font-weight: 700;
    font-size: 19px;
    line-height: 1;
    letter-spacing: 0.2px;
    text-transform: uppercase;
    white-space: nowrap;
  }
  .card__divider {
    width: 1px;
    height: 150px;
    background: var(--rule);
  }
  .card__details {
    padding-left: 26px;
  }
  .person-name {
    font-weight: 700;
    font-size: 17px;
    letter-spacing: 0.5px;
    line-height: 1.1;
  }
  .person-title {
    font-size: 12.5px;
    line-height: 1.3;
    margin-bottom: 12px;
  }
  .contact-list {
    list-style: none;
    font-size: 12.5px;
    line-height: 1.45;
    margin-bottom: 10px;
  }
  .contact-list li {
    display: flex;
    align-items: center;
    gap: 6px;
  }
  .contact-list svg {
    width: 11px;
    height: 11px;
    flex: none;
  }
  .address {
    font-size: 12.5px;
    line-height: 1.35;
    font-style: normal;
  }

  /* Back: brand side */
  .card--back {
    background: var(--card-dark);
    color: var(--paper);
    display: flex;
    align-items: center;
    justify-content: center;
    gap: 14px;
  }
  .card--back .brand-mark { width: 20px; height: 20px; }
  .card--back .brand-name { font-size: 36px; }
</style>
</head>
<body>
<main class="canvas">
  <section class="card card--front" aria-label="Business card, contact side">
    <div class="card__brand">
      <span class="brand-mark" aria-hidden="true"></span>
      <span class="brand-name">Brookvane Drafting</span>
    </div>
    <div class="card__divider" aria-hidden="true"></div>
    <div class="card__details">
      <p class="person-name">JONATHAN SMITH</p>
      <p class="person-title">Managing Director</p>
      <ul class="contact-list">
        <li>
          <svg viewBox="0 0 24 24" aria-hidden="true"><path fill="currentColor" d="M6.6 10.8a15.1 15.1 0 0 0 6.6 6.6l2.2-2.2a1 1 0 0 1 1-.25 11.4 11.4 0 0 0 3.6.57 1 1 0 0 1 1 1V20a1 1 0 0 1-1 1A17 17 0 0 1 3 4a1 1 0 0 1 1-1h3.5a1 1 0 0 1 1 1c0 1.25.2 2.45.57 3.57a1 1 0 0 1-.25 1z"/></svg>
          044-123 456 789
        </li>
        <li>
          <svg viewBox="0 0 24 24" aria-hidden="true"><path fill="currentColor" d="M2 5h20v14H2z"/><path fill="none" stroke="#f4f4f4" stroke-width="1.8" d="M2 5l10 8 10-8"/></svg>
          info@webname.com
        </li>
        <li>
          <svg viewBox="0 0 24 24" aria-hidden="true"><circle cx="12" cy="12" r="10" fill="none" stroke="currentColor" stroke-width="2"/><path fill="none" stroke="currentColor" stroke-width="1.6" d="M2 12h20M12 2c3 3 3 17 0 20M12 2c-3 3-3 17 0 20"/></svg>
          www.websitename.com
        </li>
      </ul>
      <address class="address">421, Address line goes here<br>45452,Country Name</address>
    </div>
  </section>

  <section class="card card--back" aria-label="Business card, brand side">
    <span class="brand-mark" aria-hidden="true"></span>
    <span class="brand-name">Brookvane Drafting</span>
  </section>
</main>
</body>
</html>
```